Web Developer Needs a Business Card Design

I need a personal business card design that represents me as a web developer for potential employers. I would like the background to be a dark color on the front for contrast with my logo and name. The back will have all my information along with a smaller version of the logo. I want something with a modern look and feel, not too conservative. This will be used for potential employers and freelance work.

Industry/Entity Type

Business

Contact Information for Business Card

Front should have my logo and name. The back should have all my personal information which would include: name: Tom Varulek, phone: 570-614-3098, email: tomvarulek@quillbox.net, website url: www.tomvarulek.net, logo, web developer.

Font styles to use
Sans Serif

Requirements
Must have
• Must include my logo. The color palette base color will be the logo color.

```html
<!DOCTYPE html>
<html lang="en">
<head>
<meta charset="utf-8">
<title>Tom Varulek – Business Card</title>
<link href="https://fonts.googleapis.com/css2?family=Roboto:wght@400;500&display=swap" rel="stylesheet">
<style>
  :root {
    --backdrop: #e9e4dc;
    --card: #0b0b0b;
    --teal: #6ecdb9;
    --white: #ffffff;
    --muted: #d9d9d9;
  }
  * { margin: 0; padding: 0; box-sizing: border-box; }
  html, body { width: 1200px; height: 858px; overflow: hidden; }
  body {
    background: var(--backdrop);
    font-family: "Roboto", Arial, sans-serif;
    position: relative;
  }
  .card {
    position: absolute;
    top: 279px;
    width: 525px;
    height: 300px;
    background: var(--card);
    overflow: hidden;
    box-shadow: 0 10px 28px rgba(0,0,0,.25);
  }
  .card--back { left: 45px; }
  .card--front { left: 630px; }

  .band {
    position: absolute;
    left: 0; right: 0; bottom: 0;
    height: 30px;
    background: var(--teal);
    border-top: 5px solid var(--white);
  }

  /* brand name set in the card's own text font */
  .brand {
    position: absolute;
    color: var(--teal);
    font-weight: 500;
    line-height: 1;
    white-space: nowrap;
  }

  /* information side */
  .card--back .brand {
    left: 0; width: 190px;
    top: 124px;
    text-align: center;
    font-size: 30px;
  }
  .divider {
    position: absolute;
    left: 190px; top: 30px;
    width: 1px; height: 200px;
    background: var(--muted);
  }
  .identity { position: absolute; left: 214px; top: 34px; }
  .identity__name {
    color: var(--teal);
    font-size: 36px;
    font-weight: 400;
    line-height: 1;
  }
  .identity__title {
    color: var(--white);
    font-size: 21px;
    font-weight: 500;
    margin-top: 4px;
  }
  .contacts { position: absolute; left: 214px; top: 140px; list-style: none; }
  .contacts li {
    display: flex; align-items: center; gap: 12px;
    color: var(--white);
    font-size: 15px;
    height: 27px;
  }
  .contacts svg { width: 15px; height: 15px; flex: none; }

  /* name side */
  .card--front .brand {
    right: 50px;
    top: 104px;
    font-size: 44px;
  }
  .front-name {
    position: absolute;
    left: 30px; bottom: 46px;
    color: var(--white);
    font-size: 40px;
    font-weight: 400;
  }
</style>
</head>
<body>

<section class="card card--back" aria-label="Business card, information side">
  <p class="brand">Varulek</p>
  <div class="divider"></div>
  <div class="identity">
    <h1 class="identity__name">Tom Varulek</h1>
    <p class="identity__title">Web Developer</p>
  </div>
  <ul class="contacts">
    <li>
      <svg viewBox="0 0 16 16" aria-hidden="true"><rect width="16" height="16" fill="#fff"/><path d="M5 3.5l2 2.5-1.2 1.2a6 6 0 0 0 3 3L10 9l2.5 2-1 1.5C7.5 12.5 3.5 8.5 3.5 4.5z" fill="#0b0b0b"/></svg>
      570-614-3098
    </li>
    <li>
      <svg viewBox="0 0 16 16" aria-hidden="true"><rect width="16" height="16" fill="#fff"/><rect x="3" y="4.5" width="10" height="7" fill="none" stroke="#0b0b0b" stroke-width="1.2"/><path d="M3 4.5l5 4 5-4" fill="none" stroke="#0b0b0b" stroke-width="1.2"/></svg>
      tomvarulek@quillbox.net
    </li>
    <li>
      <svg viewBox="0 0 16 16" aria-hidden="true"><rect width="16" height="16" fill="#fff"/><circle cx="8" cy="8" r="4.8" fill="none" stroke="#0b0b0b" stroke-width="1.2"/><path d="M3.2 8h9.6M8 3.2c-2 2.6-2 7 0 9.6M8 3.2c2 2.6 2 7 0 9.6" fill="none" stroke="#0b0b0b" stroke-width="1"/></svg>
      www.tomvarulek.net
    </li>
  </ul>
  <div class="band"></div>
</section>

<section class="card card--front" aria-label="Business card, name side">
  <p class="brand">Varulek</p>
  <p class="front-name">Tom Varulek</p>
  <div class="band"></div>
</section>

</body>
</html>
```